Business Card Design Project

I require a business card with the following information on them for various different people;
name
m:
f:
e:
I have a logo already and will attached that. We are in the construction industry. I require something clean and simple but eye catching at the same time. You can use another colour with our logo if you like and you can style the logo as well if you wish. I am open.
Also it needs to be front and back design.
Industry/Entity Type
Construction
Requirements
Must have
- Logo, name, mobile, fax and email address.
Front and back design

```html
<!DOCTYPE html>
<html lang="en">
<head>
<meta charset="utf-8">
<title>Hartwell Developments – Business Card</title>
<link href="https://fonts.googleapis.com/css2?family=Open+Sans:wght@400;600;700&display=swap" rel="stylesheet">
<style>
  :root {
    --backdrop: #e9e6e1;
    --card-white: #ffffff;
    --green-deep: #3a7a24;
    --green-mid: #4f9a2e;
    --green-light: #a9d14f;
    --silver: #b9bcbf;
    --silver-dark: #8d9196;
    --ink-grey: #555a5e;
    --text-white: #ffffff;
    --brand-green: #4d9a2c;
  }
  * { margin: 0; padding: 0; box-sizing: border-box; }
  html, body {
    width: 1200px; height: 407px; overflow: hidden;
    background: var(--backdrop);
    font-family: "Open Sans", Arial, sans-serif;
  }
  .stage { position: relative; width: 1200px; height: 407px; }
  .card {
    position: absolute; width: 503px; height: 288px; overflow: hidden;
    box-shadow: 3px 4px 8px rgba(0,0,0,.35);
  }
  .card--front { left: 58px; top: 60px; background: var(--card-white); }
  .card--back {
    left: 639px; top: 60px;
    background: radial-gradient(ellipse 60% 70% at 50% 48%, var(--green-light) 0%, var(--green-mid) 45%, var(--green-deep) 100%);
  }
  .front-wave { position: absolute; inset: 0; }
  .brand {
    position: absolute; left: 38px; top: 44px;
    display: flex; align-items: center; gap: 12px;
  }
  .brand__square { width: 26px; height: 26px; background: var(--brand-green); border-radius: 3px; }
  .brand__name {
    font-size: 31px; font-weight: 400; color: var(--brand-green); letter-spacing: .2px;
    line-height: 1;
  }
  .holder {
    position: absolute; left: 37px; top: 196px;
    font-size: 15px; color: var(--ink-grey);
  }
  .holder__name { font-weight: 700; }
  .holder__title { font-size: 13px; font-weight: 400; }
  .contacts {
    position: absolute; right: 20px; top: 214px;
    list-style: none; text-align: right;
  }
  .contacts li {
    display: flex; justify-content: flex-end; align-items: center; gap: 10px;
    font-size: 12.5px; color: var(--text-white); height: 21.5px;
  }
  .contacts svg { width: 11px; height: 11px; fill: var(--text-white); }
  .back-name {
    position: absolute; left: 0; right: 0; top: 115px;
    text-align: center; font-size: 44px; font-weight: 400;
    color: var(--text-white); line-height: 1;
  }
</style>
</head>
<body>
<main class="stage">
  <section class="card card--front" aria-label="Card front">
    <svg class="front-wave" viewBox="0 0 503 288" preserveAspectRatio="none" aria-hidden="true">
      <defs>
        <linearGradient id="greenFill" x1="0" y1="1" x2="1" y2="0">
          <stop offset="0" stop-color="#4c9a2d"/>
          <stop offset=".35" stop-color="#a6cf4c"/>
          <stop offset=".7" stop-color="#4a922b"/>
          <stop offset="1" stop-color="#3a7a24"/>
        </linearGradient>
        <linearGradient id="silverFill" x1="0" y1="0" x2="1" y2="0">
          <stop offset="0" stop-color="#8d9196"/>
          <stop offset=".4" stop-color="#e8e9ea"/>
          <stop offset="1" stop-color="#9da1a5"/>
        </linearGradient>
      </defs>
      <path d="M0,222 C90,250 180,262 260,200 C330,146 410,100 503,95 L503,288 L0,288 Z" fill="url(#silverFill)"/>
      <path d="M0,240 C100,268 200,270 280,208 C350,154 420,112 503,106 L503,288 L0,288 Z" fill="url(#greenFill)"/>
      <path d="M30,270 C140,290 230,262 300,205 C360,158 420,126 490,120" fill="none" stroke="#ffffff" stroke-width="1.6" opacity=".9"/>
    </svg>
    <div class="brand">
      <span class="brand__square"></span>
      <span class="brand__name">Hartwell Developments</span>
    </div>
    <p class="holder"><span class="holder__name">Your Name</span> <span class="holder__title">/ Title</span></p>
    <ul class="contacts">
      <li>123-456-7890
        <svg viewBox="0 0 24 24" aria-label="Mobile"><path d="M6.6 10.8a15.1 15.1 0 0 0 6.6 6.6l2.2-2.2c.3-.3.7-.4 1-.2 1.1.4 2.3.6 3.6.6.6 0 1 .4 1 1V20c0 .6-.4 1-1 1A17 17 0 0 1 3 4c0-.6.4-1 1-1h3.5c.6 0 1 .4 1 1 0 1.3.2 2.5.6 3.6.1.3 0 .7-.2 1z"/></svg>
      </li>
      <li>123-456-7890
        <svg viewBox="0 0 24 24" aria-label="Fax"><path d="M7 3h10v5H7zM4 9h16a2 2 0 0 1 2 2v6h-4v4H6v-4H2v-6a2 2 0 0 1 2-2zm4 7v3h8v-3z"/></svg>
      </li>
      <li>name@website.com
        <svg viewBox="0 0 24 24" aria-label="Email"><path d="M2 5h20v14H2zm2 2v.5l8 5 8-5V7z"/></svg>
      </li>
    </ul>
  </section>

  <section class="card card--back" aria-label="Card back">
    <p class="back-name">Hartwell Developments</p>
  </section>
</main>
</body>
</html>
```